Medical consulting firm needs polished website

I am a physician and working on setting up a smal consulting firm in New Hampshire, USA. It is called Bright Harbor Medical Services, LLC and the website will be BrightHarborMed.com. I was puttering around at making my own website, and it just didn't come together nicely so I've decided to leave it to the pros. The focus of the business is Advanced Care Planning, ie planning for your future medical needs. So it deals with some heavy stuff like planning for if you get sick, who should make decisions for you, end of life options etc. So it can't be too flippant or cutesy, but also can't be too dour and dark. I am hoping to convey that by thinking ahead and making some plans you can lift some of the worries off of yourself and your family - and that we can help make a scary sounding path more manageable. I want it to be made with wordpress and I have actually already bought a template ( Vitarun – A Modern Multidisciplinary Medical & Health Theme ). The website needs to have general information about our services, doc profile, appointment maker, blog/url link page, and ideally web commerce application ( the template has access to woocommerce). I've posted my business card and current brochure (still tweaking them, but you get the idea). I am also partnering with lumenfold.com and so have included their logo and would want connections/info about them. I have the logos etc in different formats as needed.

Target Market(s)

middle aged to older adults

Industry/Entity Type

Medical

Coding

Coded - Design and coding required

Font styles to use
Sans Serif

Requirements
Must have
• as above.
Nice to have
• Ease of reading/access for elderly viewers. woo commerce.

```html
<!DOCTYPE html>
<html lang="en">
<head>
<meta charset="utf-8">
<title>Bright Harbor Medical Services</title>
<link href="https://fonts.googleapis.com/css2?family=Open+Sans:wght@400;600;700&display=swap" rel="stylesheet">
<style>
:root{
  --blue:#1b6cbf;
  --blue-dark:#12539a;
  --green:#38a846;
  --ink:#333a40;
  --muted:#7a8087;
  --line:#e4e7ea;
  --soft:#f4f6f8;
  --white:#fff;
}
*{box-sizing:border-box;margin:0;padding:0}
html,body{width:1200px;height:3327px;overflow:hidden}
body{font-family:"Open Sans",Arial,sans-serif;color:var(--ink);background:var(--white);font-size:13px;line-height:1.7}
.wrap{width:1028px;margin:0 auto;position:relative}
svg{display:block}

/* header */
.topbar{height:89px}
.topbar .wrap{height:89px;display:flex;align-items:center}
.brand{display:flex;align-items:center;gap:10px;width:435px}
.brand-dot{width:40px;height:40px;border-radius:50%;background:var(--blue)}
.brand-name{font-size:24px;font-weight:700;color:var(--blue);letter-spacing:-.3px}
.info{display:flex;align-items:center;gap:10px;font-size:11px;line-height:1.5;color:var(--muted)}
.info b{display:block;font-weight:400;color:var(--ink)}
.info.hours{width:255px}
.info.call{width:213px}
.social-mini{display:flex;gap:4px;margin-top:3px}
.social-mini span{width:14px;height:14px;border:1px solid #c7ccd1;border-radius:50%}

.nav{height:48px;background:var(--blue)}
.nav .wrap{height:48px;display:flex;align-items:center}
.nav a{color:var(--white);text-decoration:none;font-size:12px;font-weight:600;position:absolute}
.search{position:absolute;left:757px;width:259px;height:32px;background:var(--white);border-radius:2px;display:flex;align-items:center;justify-content:space-between;padding:0 12px;font-size:11px;color:#9aa0a6}

/* hero */
.hero{height:493px;position:relative}
.hero-photo{position:absolute;inset:0;background:linear-gradient(90deg,#f2f1ee 0%,#ece9e4 35%,#d9cbbd 60%,#c7a891 80%,#e9e3dc 100%)}
.hero .wrap{padding-top:124px}
.hero h1{font-size:27px;font-weight:700;color:var(--blue);letter-spacing:.2px}
.hero .lead{font-size:16px;color:var(--green);font-weight:600;width:520px;margin-top:12px;line-height:1.6}
.hero p.body{font-size:11.5px;color:#555;width:480px;margin-top:14px;line-height:1.85}
.btn-green{display:inline-block;margin-top:26px;background:var(--green);color:var(--white);font-size:13px;font-weight:600;padding:12px 17px;border-radius:2px}
.dots{position:absolute;left:86px;top:466px;display:flex;gap:5px}
.dots span{width:12px;height:12px;border:2px solid #8a8f94;border-radius:50%}

/* intro */
.intro{height:434px}
.intro .wrap{display:flex;padding-top:51px}
.intro-card{width:326px;margin-right:25px}
.photo{border-radius:0}
.intro-card .photo{height:206px}
.intro-card h3{font-size:14px;font-weight:700;margin-top:22px;text-transform:uppercase}
.intro-card p{font-size:11px;color:var(--muted);margin-top:10px;line-height:1.9}
.accordion{width:308px;margin-left:17px}
.acc-item{height:48px;border-bottom:1px solid var(--line);display:flex;align-items:center;justify-content:space-between;padding:0 20px;font-size:12px;color:var(--muted)}
.acc-item.open{background:#f1f2f4;border:none}
.acc-body{font-size:11px;color:var(--muted);padding:14px 0 20px;line-height:1.9;border-bottom:1px solid var(--line)}

/* help */
.help{height:560px;background:var(--soft);text-align:center}
.section-title{font-size:18px;font-weight:700;letter-spacing:.5px;text-transform:uppercase}
.section-intro{font-size:11px;color:var(--muted);width:720px;margin:14px auto 0;line-height:1.9}
.help .section-title{padding-top:37px}
.help-cards{display:flex;justify-content:space-between;margin-top:44px}
.help-card{width:323px;height:355px;background:var(--white);padding-top:32px}
.help-card svg{margin:0 auto;width:84px;height:84px}
.help-card h4{font-size:15px;font-weight:700;margin-top:22px}
.help-card p{font-size:11px;color:var(--muted);width:260px;margin:12px auto 0;line-height:1.9}
.btn-outline{display:inline-block;margin-top:18px;font-size:11px;padding:7px 16px;border:1px solid;border-radius:2px}
.c-blue{color:var(--blue)}.c-green{color:var(--green)}

/* testimonials */
.testimonials{height:379px;position:relative;text-align:center;color:var(--white)}
.testimonials .photo{position:absolute;inset:0;background:linear-gradient(90deg,#4a4744 0%,#5e5954 30%,#6c625a 55%,#544d48 80%,#3f3c3a 100%)}
.testimonials .wrap{padding-top:58px}
.testimonials .section-title{font-size:18px}
.quote{width:68px;height:68px;border:2px solid var(--white);border-radius:50%;margin:20px auto 0;display:flex;align-items:center;justify-content:center}
.testimonials p{font-size:11.5px;width:820px;margin:22px auto 0;line-height:2.8}
.stars{color:#f2b01e;font-size:13px;letter-spacing:2px;margin-top:4px}
.name{font-size:13px;margin-top:2px}

/* services */
.services{height:366px;position:relative}
.services .photo{position:absolute;left:477px;top:0;width:723px;height:366px;background:linear-gradient(90deg,rgba(255,255,255,1) 0%,#f3ece6 20%,#e4cbb6 50%,#d4b49a 70%,#eef1ea 100%)}
.services .wrap{padding-top:22px}
.services h2{font-size:18px;font-weight:700;text-transform:uppercase}
.services .section-intro{margin:10px 0 0;width:540px;text-align:left}
.svc-list{list-style:none;margin-top:16px}
.svc-list li{display:flex;align-items:center;gap:14px;font-size:11.5px;color:#555;height:45px}
.svc-list i{width:18px;height:18px;border-radius:50%;background:linear-gradient(135deg,var(--blue) 50%,var(--green) 50%)}

/* blog */
.blog{height:648px;text-align:center}
.blog .section-title{padding-top:42px}
.blog-cards{display:flex;justify-content:space-between;margin-top:40px;text-align:left}
.post{width:330px;height:453px;border:1px solid var(--line)}
.post .photo{height:208px}
.date{display:inline-block;margin:22px 0 0 14px;background:var(--blue);color:var(--white);font-size:11px;font-weight:700;padding:5px 14px}
.post h5{font-size:12.5px;font-weight:700;margin:14px 14px 0;text-transform:uppercase}
.post p{font-size:11px;color:var(--muted);margin:10px 14px 0;line-height:1.9}
.post-meta{display:flex;justify-content:space-between;align-items:center;margin:24px 14px 0;padding-top:14px;font-size:11px;color:var(--muted)}
.post-meta .counts{display:flex;gap:14px;align-items:center}
.post-meta .counts span{display:flex;gap:4px;align-items:center}
.post-meta b{color:var(--blue);font-size:11px}

/* footer */
.footer{height:310px;background:linear-gradient(180deg,#2a86d6 0%,#1c64b5 100%);color:var(--white);position:relative}
.footer .wrap{display:flex;padding-top:38px}
.f-brand{width:340px;display:flex;align-items:center;gap:10px;padding-top:90px;padding-left:3px;height:130px}
.f-brand .dot{width:44px;height:44px;border-radius:50%;background:var(--white)}
.f-brand span{font-size:34px;font-weight:400}
.f-col h6{font-size:15px;font-weight:700;letter-spacing:.5px;margin-bottom:16px;text-transform:uppercase}
.f-contact{width:233px}
.f-contact li{list-style:none;display:flex;gap:10px;font-size:10.5px;line-height:1.5;margin-bottom:12px;align-items:flex-start}
.f-contact svg{flex:none;margin-top:2px}
.f-news{width:246px}
.f-news p{font-size:11px;line-height:1.7}
.f-input{width:210px;height:32px;background:var(--white);color:#8a9096;font-size:10.5px;padding:7px 10px;margin-top:12px}
.f-btn{display:inline-block;background:var(--green);font-size:10px;padding:4px 8px;margin-top:10px}
.f-follow{width:210px}
.f-follow p{font-size:10.5px;line-height:1.6}
.f-social{display:flex;gap:9px;margin-top:16px}
.f-social span{width:36px;height:36px;border:2px solid var(--white);border-radius:50%}
.copy{position:absolute;left:0;right:0;top:206px;text-align:center;font-size:11px;border-top:none}
.copy-line{position:absolute;left:0;right:0;top:190px;height:1px;background:rgba(255,255,255,.15)}
</style>
</head>
<body>

<header class="topbar">
  <div class="wrap">
    <div class="brand"><span class="brand-dot"></span><span class="brand-name">Bright Harbor</span></div>
    <div class="info hours">
      <svg width="26" height="26" viewBox="0 0 26 26"><circle cx="13" cy="13" r="11" fill="none" stroke="#1b6cbf" stroke-width="2"/><path d="M13 7v6l4 3" fill="none" stroke="#1b6cbf" stroke-width="2"/></svg>
      <div><b>Monday - Friday 08:00 -20:00</b>Saturday and Sunday - CLOSED</div>
    </div>
    <div class="info call">
      <svg width="20" height="26" viewBox="0 0 20 26"><rect x="2" y="1" width="16" height="24" rx="3" fill="none" stroke="#1b6cbf" stroke-width="2"/><circle cx="10" cy="20" r="1.5" fill="#1b6cbf"/></svg>
      <div><b>Call Us : (603) 555-0142</b>info@brightharbormed.com</div>
    </div>
    <div class="info">
      <svg width="26" height="24" viewBox="0 0 26 24"><path d="M3 11h5v11H3zM8 12l5-9c2 0 3 1 2 5h7c2 0 2 2 1 3l-3 10H8" fill="none" stroke="#1b6cbf" stroke-width="2"/></svg>
      <div><b>Follow Us</b><div class="social-mini"><span></span><span></span><span></span><span></span><span></span></div></div>
    </div>
  </div>
</header>

<nav class="nav">
  <div class="wrap">
    <a style="left:43px">HOME</a>
    <a style="left:142px">ABOUT US</a>
    <a style="left:273px">SERVICES</a>
    <a style="left:402px">PORTFOLIO</a>
    <a style="left:539px">BLOG</a>
    <a style="left:635px">CONTACT US</a>
    <div class="search">SEARCH<svg width="12" height="12" viewBox="0 0 12 12"><circle cx="5" cy="5" r="4" fill="none" stroke="#555" stroke-width="1.5"/><path d="M8 8l3 3" stroke="#555" stroke-width="1.5"/></svg></div>
  </div>
</nav>

<section class="hero">
  <div class="hero-photo" role="img" aria-label="Smiling family of parents and three children gathered together"></div>
  <div class="wrap">
    <h1>BRIGHT HARBOR MEDICAL SERVICES</h1>
    <p class="lead">The focus of the company is Advanced Care Planning, ie planning for your future medical needs.</p>
    <p class="body">We help you think ahead about your care, choose who will speak for you, and put clear wishes on paper so that your family can feel at ease.</p>
    <span class="btn-green">READ MORE INFO</span>
  </div>
  <div class="dots"><span></span><span></span><span></span><span></span></div>
</section>

<section class="intro">
  <div class="wrap">
    <article class="intro-card">
      <div class="photo" role="img" aria-label="Family of four smiling outdoors" style="background:linear-gradient(135deg,#c9d8c2,#d7b8a0 55%,#8fa27c)"></div>
      <h3>Contrary to Popular</h3>
      <p>Planning early lets you share your wishes calmly, so loved ones are never left guessing when care choices have to be made.</p>
    </article>
    <article class="intro-card">
      <div class="photo" role="img" aria-label="Parents and children relaxing together at home" style="background:linear-gradient(135deg,#efe9e2,#dcc2ac 55%,#c9a68b)"></div>
      <h3>Contrary to Popular</h3>
      <p>Our physician guides you step by step through each document, answering questions plainly and at a pace that suits you.</p>
    </article>
    <div class="accordion">
      <div class="acc-item open">Contrary to Popular belief<span>–</span></div>
      <div class="acc-body">A short talk today can spare your family hard choices later, and bring real peace of mind to everyone.</div>
      <div class="acc-item">Contrary to Popular belief<span>+</span></div>
      <div class="acc-item">Contrary to Popular belief<span>+</span></div>
      <div class="acc-item">Contrary to Popular belief<span>+</span></div>
      <div class="acc-item">Contrary to Popular belief<span>+</span></div>
    </div>
  </div>
</section>

<section class="help">
  <div class="wrap">
    <h2 class="section-title">We Are Here For You</h2>
    <p class="section-intro">From the first conversation to your finished directives, we walk beside you with patient, practical support so that planning ahead feels manageable instead of frightening for you and your family.</p>
    <div class="help-cards">
      <div class="help-card">
        <svg viewBox="0 0 84 84"><rect x="18" y="12" width="48" height="64" rx="4" fill="none" stroke="#1b6cbf" stroke-width="3"/><rect x="32" y="7" width="20" height="10" rx="2" fill="#fff" stroke="#1b6cbf" stroke-width="3"/><g stroke="#1b6cbf" stroke-width="3" fill="none"><path d="M26 32l3 3 5-6M26 46l3 3 5-6M26 60l3 3 5-6"/><path d="M40 32h18M40 46h18M40 60h18"/></g></svg>
        <h4 class="c-blue">PLANNING</h4>
        <p>We help you decide what matters most and record those choices in clear, lasting documents.</p>
        <span class="btn-outline c-blue">READ MORE</span>
      </div>
      <div class="help-card">
        <svg viewBox="0 0 84 84"><g fill="none" stroke="#38a846" stroke-width="3"><circle cx="42" cy="30" r="9"/><path d="M42 12v6M42 42v6M24 30h6M54 30h6M29 17l4 4M51 39l4 4M55 17l-4 4M33 39l-4 4"/><path d="M8 48l14 18h20M76 48L62 66H42M18 56c6-4 12-2 18 2M66 56c-6-4-12-2-18 2"/></g></svg>
        <h4 class="c-green">SERVICES</h4>
        <p>Personal consultations, family meetings and guidance on each legally binding directive.</p>
        <span class="btn-outline c-green">READ MORE</span>
      </div>
      <div class="help-card">
        <svg viewBox="0 0 84 84"><g fill="none" stroke="#1b6cbf" stroke-width="3" stroke-linejoin="round"><path d="M35 8h14v21l18-10 7 12-18 11 18 11-7 12-18-10v21H35V55L17 65l-7-12 18-11-18-11 7-12 18 10z"/><path d="M42 22v42M38 30c6 2 6 6 0 8s-6 6 4 8"/></g></svg>
        <h4 class="c-blue">MEDICAL</h4>
        <p>Physician insight into likely health paths, treatment options and what each choice means.</p>
        <span class="btn-outline c-blue">READ MORE</span>
      </div>
    </div>
  </div>
</section>

<section class="testimonials">
  <div class="photo" role="img" aria-label="Smiling older couple with family, darkened background"></div>
  <div class="wrap">
    <h2 class="section-title">Our Testimonials</h2>
    <div class="quote"><svg width="28" height="22" viewBox="0 0 28 22"><path d="M2 22V12C2 5 6 1 12 0v4c-3 1-5 3-5 7h5v11zM16 22V12c0-7 4-11 10-12v4c-3 1-5 3-5 7h5v11z" fill="#fff"/></svg></div>
    <p>Working with the team gave our whole family a sense of calm. Every question was answered with patience and care, and my wishes are now written down clearly. I finally feel that my children will not have to guess what I want if I fall ill someday.</p>
    <div class="stars">★★★★★</div>
    <div class="name">Name : Elena Marsh</div>
  </div>
</section>

<section class="services">
  <div class="photo" role="img" aria-label="Young family with baby and daughter smiling in a bright living room"></div>
  <div class="wrap">
    <h2>Our Services</h2>
    <p class="section-intro">Each service is shaped around you, offered with warmth and plain language so that every plan you make feels clear, complete and truly yours.</p>
    <ul class="svc-list">
      <li><i></i>Individualized Physician Guided Healthcare Planning</li>
      <li><i></i>Helping navigate complex medical situations</li>
      <li><i></i>Creating legally binding Advanced directives</li>
      <li><i></i>Sharing your decisions with your loved ones and your doctor</li>
      <li><i></i>Secure,accessible,web-based storage of your documents</li>
    </ul>
  </div>
</section>

<section class="blog">
  <div class="wrap">
    <h2 class="section-title">Latest Blog &amp; News</h2>
    <p class="section-intro">Read our latest articles on care planning, family conversations and the practical steps that help you and your loved ones prepare with confidence and calm.</p>
    <div class="blog-cards">
      <article class="post">
        <div class="photo" role="img" aria-label="Three generations of a family sitting outdoors" style="background:linear-gradient(135deg,#b8c9a6,#d8c3ae 55%,#8ea36f)"></div>
        <span class="date">OCT 27,2015</span>
        <h5>Contrary to Popular Belief</h5>
        <p>Why the best time to talk about future care is while you are well and able to decide.</p>
        <div class="post-meta"><div class="counts"><span>💬 5</span><span>♡ 4</span></div><b>READ MORE</b></div>
      </article>
      <article class="post">
        <div class="photo" role="img" aria-label="Family laughing together on a sofa" style="background:linear-gradient(135deg,#e8dccd,#c9a587 55%,#a88a72)"></div>
        <span class="date">OCT 27,2015</span>
        <h5>Contrary to Popular Belief</h5>
        <p>Choosing a health care agent: what to look for and how to start that conversation.</p>
        <div class="post-meta"><div class="counts"><span>💬 5</span><span>♡ 4</span></div><b>READ MORE</b></div>
      </article>
      <article class="post">
        <div class="photo" role="img" aria-label="Grandparents with grandchildren in a sunny park" style="background:linear-gradient(135deg,#f0e9de,#d7bfa4 55%,#b4bf98)"></div>
        <span class="date">OCT 27,2015</span>
        <h5>Contrary to Popular Belief</h5>
        <p>Keeping your directives safe, current and easy for family and doctors to reach.</p>
        <div class="post-meta"><div class="counts"><span>💬 5</span><span>♡ 4</span></div><b>READ MORE</b></div>
      </article>
    </div>
  </div>
</section>

<footer class="footer">
  <div class="wrap">
    <div class="f-brand"><span class="dot"></span><span>lumenfold</span></div>
    <div class="f-col f-contact">
      <h6>Contact Us</h6>
      <ul>
        <li><svg width="12" height="12" viewBox="0 0 12 12"><path d="M2 1l3 2-1 2c1 2 2 3 3 3l2-1 2 3-2 1C5 11 1 7 1 3z" fill="#fff"/></svg>603-555-0187 (Phone)</li>
        <li><svg width="12" height="12" viewBox="0 0 12 12"><rect x="1" y="4" width="10" height="7" fill="#fff"/><rect x="3" y="1" width="6" height="3" fill="#fff"/></svg>603-555-0193 (Fax)</li>
        <li><svg width="12" height="12" viewBox="0 0 12 12"><rect x="1" y="2" width="10" height="8" fill="#fff"/><path d="M1 2l5 4 5-4" stroke="#1c64b5" fill="none"/></svg><u>info@brightharbormed.com</u></li>
        <li><svg width="12" height="12" viewBox="0 0 12 12"><path d="M6 11S2 7 2 4.5a4 4 0 018 0C10 7 6 11 6 11z" fill="#fff"/></svg>Unit #4, 27 Harbor Lane<br>Concord NH</li>
      </ul>
    </div>
    <div class="f-col f-news">
      <h6>Newsletter</h6>
      <p>Register Your email address to get information about us</p>
      <div class="f-input">Email Address</div>
      <span class="f-btn">SUBSCRIBE</span>
    </div>
    <div class="f-col f-follow">
      <h6>Follow Us</h6>
      <p>Stay in touch for care planning tips, event news and gentle reminders.</p>
      <div class="f-social"><span></span><span></span><span></span><span></span><span></span></div>
    </div>
  </div>
  <div class="copy-line"></div>
  <div class="copy" style="top:280px">© Copyright 2016 Bright Harbor Med. All rights reserved</div>
</footer>

</body>
</html>
```